Camp Maplebrook 2018

We need a postcard design to advertise our summer programs. We are a Christian camp with day camp and overnight camps.

Target Market(s)

parents of elementary age kids

Industry/Entity Type

Christian

Colors
ec1f27
f37122
faa54b
fbee3d
f78f20
f04a50
fbed22
fbee3e

Requirements
Must have
• Day Camp 2018 "Shine Bright Daily"
• June 25 - August 24
• $135 per week
• Mon-Fri 8 am to 4 pm. Open to all kids entering grades 1 to 8. Day camp is chock full of activities like swimming, rock wall, archery, sports, crafts, air rifles and much more! Daily lunch and snack included. Before and after-care available at an extra rate.
• Register and pay in full by April 1st, save $270!
• Overnight Camp 2018
• July 15 - 21 & July 22 - 28
• $330 per week
• Open to all kids ages 8 to 14. Spend the week making new friends, sleeping in cabins, climbing the rock wall and swimming at the beach! Our guest speakers will lead twice daily chapel sessions that will challenge campers to grow in their faith.
• 42 Cedar Vale Rd. Barrington, NH 03819
• 603-418-5926
• www.maplebrook.org
Nice to have
• bright and colorful

```html
<!DOCTYPE html>
<html lang="en">
<head>
<meta charset="utf-8">
<title>Camp Maplebrook 2018 Postcard</title>
<link rel="stylesheet" href="https://fonts.googleapis.com/css2?family=Oswald:wght@400;500;700&family=Josefin+Sans:wght@600;700&family=Catamaran:wght@400;500&family=Great+Vibes&display=swap">
<style>
  :root {
    --red: #d3182b;
    --orange-red: #e0321f;
    --orange: #f37122;
    --brown: #7a4a22;
    --ink: #1a1a1a;
    --blush: #fbe3e6;
    --paper: #ffffff;
    --backdrop: #5b5e61;
    --rule: #d9d9d9;
  }
  * { box-sizing: border-box; margin: 0; padding: 0; }
  html, body { width: 1200px; height: 675px; overflow: hidden; }
  body { background: var(--backdrop); position: relative; font-family: "Catamaran", sans-serif; }

  .postcard { position: absolute; top: 128px; width: 560px; height: 420px; background: var(--paper); overflow: hidden; }
  .postcard--front { left: 25px; }
  .postcard--back { left: 615px; }
  .postcard svg.art { position: absolute; inset: 0; }

  /* front */
  .front-copy { position: absolute; right: 26px; top: 24px; width: 300px; text-align: right; }
  .headline { font-family: "Oswald", sans-serif; font-weight: 700; color: var(--red); font-size: 29px; line-height: 1; letter-spacing: .3px; }
  .tagline { font-family: "Great Vibes", cursive; color: var(--brown); font-size: 31px; line-height: 1; margin-top: 1px; }
  .date-band { display: inline-block; background: var(--orange-red); color: #fff; font-family: "Josefin Sans", sans-serif; font-weight: 600; font-size: 16px; letter-spacing: 1.2px; padding: 5px 8px 2px; margin-top: 5px; white-space: nowrap; }
  .price { font-family: "Josefin Sans", sans-serif; font-weight: 700; color: var(--red); font-size: 42px; line-height: 1; margin-top: 10px; }
  .per-week { font-family: "Oswald", sans-serif; font-weight: 400; color: var(--brown); font-size: 21px; line-height: 1.1; }
  .details { font-size: 10.2px; line-height: 1.22; color: var(--ink); margin-top: 8px; margin-left: auto; width: 268px; }
  .early { font-family: "Oswald", sans-serif; font-weight: 400; font-size: 15.5px; color: var(--ink); margin-top: 12px; letter-spacing: -.2px; white-space: nowrap; }
  .save { font-family: "Josefin Sans", sans-serif; font-weight: 700; color: var(--orange-red); font-size: 38px; line-height: 1; margin-top: 2px; white-space: nowrap; }

  .brand { position: absolute; right: 26px; bottom: 26px; display: flex; align-items: center; gap: 10px; }
  .brand-mark { width: 30px; height: 30px; border-radius: 50%; background: var(--orange); }
  .brand-name { font-family: "Josefin Sans", sans-serif; font-weight: 700; font-size: 30px; color: var(--red); line-height: 1; padding-top: 5px; white-space: nowrap; }

  /* back */
  .overnight-title { position: absolute; left: 24px; top: 96px; font-family: "Oswald", sans-serif; font-weight: 700; font-size: 37px; line-height: .95; color: var(--red); -webkit-text-stroke: 3px #fff; paint-order: stroke fill; }
  .back-copy { position: absolute; left: 22px; top: 176px; width: 300px; }
  .back-copy .date-band { margin-top: 0; font-family: "Oswald", sans-serif; font-weight: 400; letter-spacing: .2px; font-size: 15px; padding: 2px 8px; }
  .back-copy .price { margin-top: 6px; font-size: 38px; }
  .back-copy .per-week { margin-left: 3px; font-size: 20px; line-height: 1; }
  .back-copy .details { width: 258px; margin: 7px 0 0 2px; font-size: 9.4px; line-height: 1.2; text-align: justify; }
  .contact { display: flex; margin-top: 9px; margin-left: 2px; }
  .contact-item { font-family: "Oswald", sans-serif; line-height: 1.1; white-space: nowrap; }
  .contact-item + .contact-item { border-left: 1.5px solid var(--ink); margin-left: 8px; padding-left: 8px; }
  .contact-label { font-weight: 700; font-size: 15px; color: var(--ink); }
  .contact-value { font-weight: 700; font-size: 15px; color: var(--red); white-space: nowrap; }
  .address { position: absolute; left: 40px; bottom: 9px; color: #fff; font-size: 10px; font-weight: 500; white-space: nowrap; }

  .stamp-box { position: absolute; right: 28px; top: 22px; width: 67px; height: 67px; border: 1px solid #e2e2e2; }
  .to-label { position: absolute; left: 313px; top: 115px; font-size: 12px; color: var(--ink); }
  .address-line { position: absolute; left: 322px; width: 208px; border-top: 1px solid var(--rule); }
</style>
</head>
<body>

<section class="postcard postcard--front" aria-label="Day camp postcard, front">
  <svg class="art" width="560" height="420" viewBox="0 0 560 420">
    <path d="M280,0 H345 C290,90 305,200 292,290 C284,350 292,395 302,420 H210 C215,390 225,340 240,290 C268,200 242,90 280,0Z" fill="var(--blush)"/>
    <defs>
      <linearGradient id="frontPhoto" x1="0" y1="0" x2="1" y2="1">
        <stop offset="0" stop-color="#8a7462"/>
        <stop offset=".5" stop-color="#c9a184"/>
        <stop offset="1" stop-color="#4a4f5a"/>
      </linearGradient>
    </defs>
    <path role="img" aria-label="Photo of a smiling girl at camp" d="M0,0 H280 C242,90 268,200 240,290 C225,340 215,390 210,420 H0Z" fill="url(#frontPhoto)"/>
  </svg>

  <div class="front-copy">
    <h1 class="headline">DAY CAMP 2018</h1>
    <p class="tagline">Shine Bright Daily</p>
    <p class="date-band">JUNE 25 – AUGUST 24</p>
    <p class="price">$135</p>
    <p class="per-week">PER WEEK</p>
    <p class="details">Mon-Fri 8 am to 4 pm. Open to all kids entering grades 1 to 8. Day camp is chock full of activities like swimming, rock wall, archery, sports, crafts, air rifles and much more! Daily lunch and snack included. Before and after-care available at an extra rate.</p>
    <p class="early">REGISTER &amp; PAY IN FULL BY APRIL 1ST</p>
    <p class="save">SAVE $270</p>
  </div>

  <div class="brand">
    <span class="brand-mark"></span>
    <span class="brand-name">Camp Maplebrook</span>
  </div>
</section>

<section class="postcard postcard--back" aria-label="Overnight camp postcard, back">
  <svg class="art" width="560" height="420" viewBox="0 0 560 420">
    <defs>
      <linearGradient id="backPhoto" x1="0" y1="0" x2="1" y2="1">
        <stop offset="0" stop-color="#6e7a6a"/>
        <stop offset=".45" stop-color="#b8a38a"/>
        <stop offset="1" stop-color="#c9783c"/>
      </linearGradient>
    </defs>
    <path d="M0,150 C30,170 70,178 110,176 L0,200Z" fill="var(--red)"/>
    <path role="img" aria-label="Photo of campers wrapped in towels on the beach" d="M0,0 H295 C308,45 300,112 262,145 C222,176 150,182 100,172 C60,165 28,168 0,178Z" fill="url(#backPhoto)"/>
    <path d="M288,40 C300,92 290,132 262,156 C230,180 180,186 140,182" fill="none" stroke="var(--red)" stroke-width="4"/>
    <path d="M0,398 C120,384 300,388 420,394 C480,397 530,394 560,384 V420 H0Z" fill="var(--red)"/>
  </svg>

  <h2 class="overnight-title">OVERNIGHT<br>CAMP 2018</h2>

  <div class="back-copy">
    <p class="date-band">JULY 15 - 21 &amp; JULY 22 - 28</p>
    <p class="price">$330</p>
    <p class="per-week">PER WEEK</p>
    <p class="details">Open to all kids ages 8 to 14. Spend the week making new friends, sleeping in cabins, climbing the rock wall and swimming at the beach! Our guest speakers will lead twice daily chapel sessions that will challenge campers to grow in their faith.</p>
    <div class="contact">
      <div class="contact-item">
        <p class="contact-label">CALL US</p>
        <p class="contact-value">603-418-5926</p>
      </div>
      <div class="contact-item">
        <p class="contact-label">VISIT US</p>
        <p class="contact-value">WWW.MAPLEBROOK.ORG</p>
      </div>
    </div>
  </div>

  <p class="address">42 Cedar Vale Rd. Barrington, NH 03819</p>

  <div class="stamp-box"></div>
  <p class="to-label">To</p>
  <div class="address-line" style="top:168px"></div>
  <div class="address-line" style="top:200px"></div>
  <div class="address-line" style="top:230px"></div>
  <div class="address-line" style="top:264px"></div>
</section>

</body>
</html>
```